Lev Marchetti - Senior Living Audio CDs - CD Design and Cover Design

I am an executive director in an assisted living facility. I have just started speaking, training, and coaching in the Senior Living Industry. I have 4 audio files that I want to put to a CD. The names of the CD's are:

1- Leadership - Creating A Culture of Excellence in Senior Living
2- The Purpose of Your Senior Living Business
3- A Leaders Vision - Your Attention Becomes Your Intention
4- Group Interviews -A Secret in Employee Retention

I think I can use the same CD cover for each CD. I just need the same design but 4 different ones with the names above. So everything will be the same but the name change. The inside cover will be I will consider other colors but it would be great if it would look good with the logo. I also need help with designing the CD face itself. I will be using a standard Jewel CD case. I need the front cover, the inside cover, and the back. The logo will be on all three.

On the front:

Part of me thinks it should be a clean simple design with my logo, my picture, and the title. But I am also curious about the picture of me with the elderly lady. - I need the 4 designs that are the same except the title.

On the Inside:

It can be the same design but the wording will be specific to that CD and the 4 insides will be:

All businesses rise and fall with leadership. This is especially true in the senior living industry. The life of that rise or fall is based on the culture the leader creates. Learn the 3 keys to what leaders know and do. Learn what the Importance Factor is and how you can put it to work to create and sustain a winning culture that will drive your business and occupancy above the rest.

What is the purpose of your senior living business? Your understanding to the answer of this question makes all the difference. After you have gained this understanding it takes the right beliefs and behavior of associates to fulfill this purpose. What's the purpose? How is it fulfilled?

They want a captain not a boss. As a leader in senior living you steer the ship. What you put your attention on becomes the intention of your community. Your ability to create a vision, help people embrace that vision, and learn how to stay focused when the storms of the industry come raging, is the key to your success. There is a pattern to achieving this success. Come learn this pattern and how to apply it in your life and your business. It can make all the difference.

A business can not be better than it's people. The right people are the key not just people. Learn where your focus should be to hire the right people. After you hire then find out what you can do to retain them and engage them. If you want happy residents you need happy associates.

On the back it will need to have:

1- My Logo
2- www.LevMarchetti.example
3- Email: info@LevMarchetti.example
4- You could put the picture of me and the elderly lady as a watermark on the back with the above info.

I have a short turn around time and need designs quickly. I also need help with designing the CD. My picture, the logo, and the Title.

```html
<!DOCTYPE html>
<html lang="en">
<head>
<meta charset="utf-8">
<title>Lev Marchetti – Leadership CD</title>
<link href="https://fonts.googleapis.com/css2?family=Nunito+Sans:wght@400;600;700&family=Cinzel:wght@700&display=swap" rel="stylesheet">
<style>
  :root{
    --bg:#f1f1f1;
    --cream:#e9ddb6;
    --panel-top:#3c3c3c;
    --panel-bottom:#262626;
    --ink-light:#ffffff;
    --ink-body:#a9a9a9;
    --ink-muted:#6f6f6f;
    --tab:#f7f7f7;
    --tab-text:#8a8a8a;
    --gold:#c8b27a;
    --disc-top:#5a5a5a;
    --disc-bottom:#2b2b2b;
  }
  *{box-sizing:border-box;margin:0;padding:0}
  html,body{width:1200px;height:800px;overflow:hidden;background:var(--bg)}
  body{position:relative;font-family:"Nunito Sans",Arial,sans-serif}

  .inside-cover{
    position:absolute;left:50px;top:140px;width:520px;height:520px;
    background:var(--cream);padding:22px;
  }
  .inside-cover__panel{
    position:relative;width:100%;height:100%;overflow:hidden;
    background:linear-gradient(180deg,var(--panel-top),var(--panel-bottom));
  }
  .inside-cover__headline{
    position:absolute;left:34px;top:48px;color:var(--ink-light);
    font-weight:700;font-size:17px;line-height:1.55;letter-spacing:.3px;
  }
  .inside-cover__headline span{display:block}
  .inside-cover__headline span + span{padding-left:48px}
  .inside-cover__body{
    position:absolute;left:56px;top:140px;width:250px;
    color:var(--ink-body);font-size:11.5px;line-height:1.45;
  }
  .inside-cover__portrait{
    position:absolute;left:296px;top:22px;width:150px;height:440px;
    border-radius:60px 60px 30px 30px;
    background:linear-gradient(180deg,#4a4a4a 0%,#3a3a3a 40%,#2c2c2c 100%);
  }
  .inside-cover__tab{
    position:absolute;left:0;top:340px;width:258px;height:70px;
    background:var(--tab);border-radius:0 16px 16px 0;
    display:flex;align-items:center;padding-left:24px;
    font-family:"Cinzel",Georgia,serif;font-weight:700;font-size:25px;
    letter-spacing:3px;color:var(--tab-text);
  }
  .inside-cover__byline{
    position:absolute;right:34px;bottom:22px;text-align:right;
    color:var(--ink-muted);font-size:9.5px;line-height:1.3;
  }
  .brand{
    position:absolute;left:18px;bottom:22px;display:flex;align-items:center;gap:8px;
    color:var(--ink-light);font-weight:600;font-size:13px;
  }
  .brand__dot{width:22px;height:22px;border-radius:50%;background:var(--gold)}

  .disc{position:absolute;left:605px;top:130px;width:540px;height:540px}
</style>
</head>
<body>

<section class="inside-cover" aria-label="Inside cover">
  <div class="inside-cover__panel">
    <h1 class="inside-cover__headline">
      <span>All Businesses Rise</span>
      <span>And Fall With Leadership</span>
    </h1>
    <p class="inside-cover__body">This is especially true in the senior living industry. The life of that rise or fall is based on the culture the leader creates. Learn the 3 keys to what leaders know and do. Learn what the importance factor is and how you can put it to work to create and sustain a winning culture that will drive your business and occupancy above the rest.</p>
    <div class="inside-cover__portrait" role="img" aria-label="Standing portrait of Lev Marchetti in a dark suit"></div>
    <div class="inside-cover__tab">LEADERSHIP</div>
    <p class="inside-cover__byline">By Executive Director<br>Lev Marchetti</p>
    <div class="brand"><span class="brand__dot"></span>Lev Marchetti</div>
  </div>
</section>

<svg class="disc" viewBox="0 0 540 540" role="group" aria-label="Disc face">
  <defs>
    <linearGradient id="discFill" x1="0" y1="0" x2="0" y2="1">
      <stop offset="0" stop-color="#5a5a5a"/>
      <stop offset="1" stop-color="#2b2b2b"/>
    </linearGradient>
  </defs>
  <circle class="disc__face" cx="270" cy="270" r="268" fill="url(#discFill)" stroke="#cfcfcf" stroke-width="2"/>
  <circle class="disc__hub-ring" cx="270" cy="270" r="62" fill="#9a9a9a" opacity=".35"/>
  <circle class="disc__hub" cx="270" cy="270" r="44" fill="#d8d8d8" opacity=".45" stroke="#bdbdbd"/>
  <circle class="disc__hole" cx="270" cy="270" r="17" fill="#f1f1f1"/>
  <text x="270" y="118" text-anchor="middle" fill="#9a9a9a"
        font-family="Cinzel, Georgia, serif" font-weight="700" font-size="24" letter-spacing="3">1. LEADERSHIP</text>
  <text x="270" y="146" text-anchor="middle" fill="#9a9a9a"
        font-family="Nunito Sans, Arial, sans-serif" font-size="13.5">Creating A Culture Of Excellence In Senior Living</text>
  <circle cx="214" cy="182" r="8" fill="#c8b27a"/>
  <text x="228" y="187" fill="#bdbdbd" font-family="Nunito Sans, Arial, sans-serif" font-weight="600" font-size="13">Lev Marchetti</text>
</svg>

</body>
</html>
```